We are building a website where users come to see what skills they will need for their career. The content of the page is data-driven, so the site should have the feel of a set of data dashboards. The data is collected and processed using machine learning. The main idea is for the user to come in and spend some minutes exploring, scrolling and clicking around.
The task is to design a website with four pages:
Front page
Early career page
Skill trends page
Skills Page
Each of these is described in attached files, along with example data
We need the resulting files to be exported also to uncompressed PNG, and in the case of vector graphics, to SVG.
Target Market(s)
People Looking to start a Career and Policy makers.
Industry/Entity Type
Human Resource
Number of Pages Required
4 page
Look and feel

```html
<!DOCTYPE html>
<html lang="en">
<head>
<meta charset="utf-8">
<title>Talentmap – Your personal guide to the skill trends</title>
<link href="https://fonts.googleapis.com/css2?family=Montserrat:wght@300;400;500;600;700&family=Space+Mono:ital,wght@1,700&display=swap" rel="stylesheet">
<style>
:root{
  --ink:#1c1c1c;
  --text:#7a7a7a;
  --accent:#1493d9;
  --accent-soft:#5db8e2;
  --panel:#efefef;
  --footer:#000;
  --white:#fff;
  --tag:#7c6ee0;
}
*{margin:0;padding:0;box-sizing:border-box}
html,body{width:1200px;height:4914px;overflow:hidden;background:var(--white)}
body{position:relative;font-family:"Montserrat",sans-serif;color:var(--ink)}

/* header */
.site-header{position:absolute;left:0;top:0;width:1200px;height:76px;background:var(--white)}
.brand{position:absolute;left:99px;top:18px;font-size:34px;font-weight:400;letter-spacing:5px;color:var(--ink)}
.main-nav a{position:absolute;top:30px;font-size:14px;letter-spacing:1.6px;color:var(--ink);text-decoration:none;font-weight:500}
.main-nav a.active{color:var(--accent)}

/* hero */
.hero{position:absolute;left:0;top:76px;width:1200px;height:611px;background:linear-gradient(115deg,#0a2f5c 0%,#0b4f86 38%,#0a8ac2 70%,#00e5f0 100%)}
.hero-art{position:absolute;left:19px;top:40px;width:611px;height:535px;border-radius:8px;background:radial-gradient(ellipse at 50% 45%,#1fa6d8 0%,#0d5d92 45%,rgba(10,47,92,0) 75%)}
.hero-title{position:absolute;left:637px;top:152px;font-size:66px;font-weight:300;letter-spacing:9px;color:var(--white)}
.hero-sub{position:absolute;left:637px;top:238px;font-size:22px;font-weight:600;line-height:31px;letter-spacing:.8px;color:var(--white)}

/* shared */
.section-title{position:absolute;left:0;width:1200px;text-align:center;font-size:54px;font-weight:300;letter-spacing:7px;color:var(--ink);line-height:58px}
.block-title{position:absolute;font-weight:300;color:var(--ink);letter-spacing:5px}
.copy{position:absolute;font-size:14.5px;line-height:29.5px;color:var(--text);text-align:justify}
.btn{position:absolute;display:flex;align-items:center;justify-content:center;height:44px;border-radius:22px;background:var(--accent);color:var(--white);font-size:14px;font-weight:500;text-decoration:none}
.frame-back{position:absolute;background:var(--accent-soft);border-radius:70px}
.frame-img{position:absolute;border-radius:70px 100px 70px 100px;overflow:hidden}
.img-network{background:radial-gradient(circle at 65% 40%,#33d0e8 0%,#0d6f8f 30%,#062c44 70%,#04182a 100%)}
.img-brain{background:radial-gradient(circle at 50% 38%,#3ad3ff 0%,#0a5a8e 28%,#061f36 62%,#020b16 100%)}
.img-circuit{background:radial-gradient(circle at 62% 45%,#2a8fc0 0%,#0c3e63 45%,#04172a 100%)}

/* steps */
.step-num{position:absolute;font-size:92px;font-weight:700;color:#e9e9e9;letter-spacing:-2px;line-height:1}
.step-line{position:absolute;height:1px;background:#e0e0e0}
.step-label{position:absolute;left:254px;top:1456px;font-size:21px;font-weight:600;letter-spacing:1.5px;line-height:31px;color:var(--ink)}
.lang{position:absolute;left:254px;top:1530px;font-size:13px;color:#9a9a9a;letter-spacing:1px}
.card{position:absolute;background:var(--white);box-shadow:0 2px 8px rgba(0,0,0,.18);overflow:hidden}
.legend,.axis{font-family:"Space Mono",monospace;font-style:italic;font-weight:700;font-size:8.5px;fill:#222}

.ad{padding:8px 7px;font-size:8px;line-height:12.2px;color:#333}
.tag{display:inline-block;border:1px solid var(--tag);border-radius:2px;color:var(--tag);padding:0 4px;line-height:10px;margin:1px 0}
.ad-gap{height:8px}
.vote{position:absolute;left:7px;bottom:8px;width:299px;height:24px;display:flex}
.vote span{flex:1;display:flex;align-items:center;justify-content:center;border:1px solid}
.vote .up{border-color:#3fbf6a}
.vote .down{border-color:#e5484d;border-left:none}

/* about */
.about-band{position:absolute;left:0;top:3392px;width:1200px;height:567px;background:var(--panel)}
.about-copy{position:absolute;left:160px;width:880px;text-align:center;font-size:14.5px;line-height:25px;color:var(--text)}
.team-photo{position:absolute;top:3826px;width:304px;height:282px;border-radius:60px 60px 8px 60px}
.ph-1{background:linear-gradient(160deg,#cfcac2,#8e8a82 60%,#3b3a38)}
.ph-2{background:linear-gradient(160deg,#d8d4cd,#a08d78 55%,#4a4440)}
.ph-3{background:linear-gradient(160deg,#d2d0cc,#8d8a86 55%,#2f2f30)}

/* sources */
.source{position:absolute;display:flex;align-items:center;gap:10px;font-size:22px;font-weight:600;color:var(--ink)}
.source i{display:block;width:22px;height:22px;background:var(--ink)}

/* footer */
.site-footer{position:absolute;left:0;top:4579px;width:1200px;height:335px;background:var(--footer);color:var(--white)}
.f-head{position:absolute;top:55px;font-size:22px;font-weight:600}
.f-text{position:absolute;font-size:13px;line-height:23px;color:var(--white)}
.f-input{position:absolute;left:408px;top:162px;width:298px;height:35px;background:var(--white);display:flex;align-items:center;padding:0 14px;font-size:12px;color:#9a9a9a;justify-content:space-between}
.copyright{position:absolute;left:0;top:303px;width:1200px;text-align:center;font-size:11px;color:var(--white)}
</style>
</head>
<body>

<header class="site-header">
  <div class="brand">TALENTMAP</div>
  <nav class="main-nav">
    <a class="active" style="left:559px" href="#">HOME</a>
    <a style="left:666px" href="#">EARLY CAREER</a>
    <a style="left:857px" href="#">SKILL TRENDS</a>
    <a style="left:1040px" href="#">SKILLS</a>
  </nav>
</header>

<section class="hero">
  <div class="hero-art" role="img" aria-label="Isometric laptop with glowing data screens and connected skill icons"></div>
  <h1 class="hero-title">TALENTMAP</h1>
  <p class="hero-sub">Your personal guide to the skill trends<br>on the job market</p>
</section>

<div class="frame-back" style="left:82px;top:790px;width:445px;height:400px;transform:rotate(-6deg)"></div>
<div class="frame-img img-network" style="left:97px;top:805px;width:428px;height:393px" role="img" aria-label="Glowing neural network of connected nodes"></div>
<h2 class="block-title" style="left:591px;top:858px;font-size:54px">MOTIVATION</h2>
<p class="copy" style="left:593px;top:935px;width:506px">We enable deep and unbiased analysis of the skill demands in the job market. Using deep learning techniques, we achieve understanding of job advertisements to extract the most relevant information for you. We combine these analysis with the most complete structural knowledge repositories to deliver analytics, discover trends and provide recommendations for personal professional development, as well as insightful job market overviews!</p>

<h2 class="section-title" style="top:1312px">3 DIFFERENT<br>WAYS TO PROCEED</h2>

<div class="step-label">ENTER A SKILL OR<br>A JOB TITLE</div>
<div class="lang">EN &#8964;</div>
<div class="step-line" style="left:462px;top:1496px;width:196px"></div>
<div class="step-num" style="left:668px;top:1452px">01</div>

<div class="step-num" style="left:305px;top:1613px">02</div>
<div class="step-line" style="left:422px;top:1656px;width:93px"></div>
<div class="card" style="left:521px;top:1580px;width:427px;height:156px">
  <svg width="427" height="156" viewBox="0 0 427 156">
    <circle cx="10" cy="17" r="2.5" fill="#3a5cd8"/><text class="legend" x="16" y="10">Project</text><text class="legend" x="16" y="19">Management</text><text class="legend" x="16" y="28">Skills</text>
    <circle cx="90" cy="17" r="2.5" fill="#e2463b"/><text class="legend" x="96" y="20">Pedagogy</text>
    <circle cx="168" cy="17" r="2.5" fill="#e3b21c"/><text class="legend" x="190" y="10">Use of</text><text class="legend" x="190" y="19">Office</text><text class="legend" x="190" y="28">Software</text>
    <circle cx="256" cy="17" r="2.5" fill="#2bb04a"/><text class="legend" x="262" y="10">Alternative</text><text class="legend" x="262" y="19">Teaching</text><text class="legend" x="262" y="28">Techniques</text>
    <circle cx="352" cy="17" r="2.5" fill="#b43cc8"/><text class="legend" x="358" y="10">Human</text><text class="legend" x="358" y="19">Resource</text><text class="legend" x="358" y="28">Management</text>
    <g stroke="#eee" stroke-width="1"><line x1="20" y1="52" x2="415" y2="52"/><line x1="20" y1="75" x2="415" y2="75"/><line x1="20" y1="98" x2="415" y2="98"/><line x1="20" y1="121" x2="415" y2="121"/></g>
    <polyline fill="none" stroke="#3a5cd8" stroke-width="1.4" points="25,58 50,62 80,60 110,63 140,61 170,70 200,66 230,65 260,68 290,69 320,66 350,72 380,69 410,74"/>
    <polyline fill="none" stroke="#e2463b" stroke-width="1.4" points="25,62 55,68 85,71 115,76 145,72 175,79 205,75 235,84 250,66 265,86 290,78 320,82 340,70 360,84 390,74 410,80"/>
    <polyline fill="none" stroke="#b43cc8" stroke-width="1.4" points="25,74 60,77 95,78 130,79 165,80 200,81 235,82 270,82 305,83 340,83 375,84 410,85"/>
    <polyline fill="none" stroke="#e3b21c" stroke-width="1.4" points="25,96 60,98 95,97 130,99 165,100 200,99 235,101 270,100 305,102 340,102 375,103 410,101"/>
    <polyline fill="none" stroke="#2bb04a" stroke-width="1.4" points="25,118 80,119 140,119 200,120 260,120 320,120 370,120 390,116 400,104 408,78 412,60"/>
    <text class="axis" x="26" y="146">2015</text><text class="axis" x="88" y="146">2016</text><text class="axis" x="150" y="146">2017</text><text class="axis" x="212" y="146">2018</text><text class="axis" x="274" y="146">2019</text><text class="axis" x="336" y="146">2020</text><text class="axis" x="396" y="146">2021</text>
  </svg>
</div>

<div class="card" style="left:254px;top:1786px;width:313px;height:418px">
  <div class="ad">
    Ihre Aufgaben<br>
    als Sales Mitarbeiter (m/w/d) bist Du erster Ansprechpartner des Unternehmens und verantwortlich für die freundliche und kompetente Betreuung, <span class="tag">Beratung</span><br>
    und Akquise von Neukunden<br>
    Bearbeitung von Anfragen und Versand von Informationsmaterialien<br>
    Erarbeiten von Angeboten, deren Verfolgung und Betreuung bis zur Auftragserteilung<br>
    Verkauf unserer Produkte per Telefon<br>
    Akquise von Neukunden<br>
    Enge Zusammenarbeit mit allen Bereichen des Unternehmens, intensive<br>
    <span class="tag">Kommunikation</span> <span class="tag">Kommunikation</span> mit dem Bereich <span class="tag">Kundendienst</span><br>
    <span class="tag">Beratung</span> sgespräche bei Messen
    <div class="ad-gap"></div>
    Das bringen Sie mit<br>
    als Sales Mitarbeiter (m/w/d) hast Du eine abgeschlossene kaufmännische Berufsausbildung<br>
    Sowie idealerweise zwei Jahre Vertriebserfahrung (nicht unbedingt erforderlich)<br>
    Selbständigkeit und Eigeninitiative sind für Dich selbstverständlich wie ein sicheres Auftreten und Kundenorientierung<br>
    Du verfügst über sehr gute <span class="tag">Deutsch</span> <span class="tag">Deutschkenntnisse</span> in Sprache und Schrift sowie Grundkenntnisse in <span class="tag">Englisch</span> <span class="tag">Englisch</span><br>
    Ehrgeizige Verkaufsziele sind für Dich kein Stressfaktor, sondern eine Herausforderung und Gelegenheit, zum Unternehmenserfolg beizutragen und Dich zu beweisen<br>
    Sehr gute Networking- und <span class="tag">Kommunikation</span> sfähigkeiten bringst Du außerdem mit
  </div>
  <div class="vote">
    <span class="up"><svg width="12" height="12" viewBox="0 0 12 12"><path d="M2 6h2v5H2zM5 11h4.5l1.5-4.5V5.5H7.5L8 2.5 7 1.5 5 5.5z" fill="none" stroke="#3fbf6a"/></svg></span>
    <span class="down"><svg width="12" height="12" viewBox="0 0 12 12"><path d="M2 1h2v5H2zM5 1h4.5L11 5.5v1H7.5L8 9.5 7 10.5 5 6.5z" fill="none" stroke="#e5484d"/></svg></span>
  </div>
</div>
<div class="step-line" style="left:567px;top:1996px;width:110px"></div>
<div class="step-num" style="left:686px;top:1952px">03</div>

<h2 class="section-title" style="top:2306px">OUR APPLICATION</h2>

<h3 class="block-title" style="left:101px;top:2462px;font-size:31px">CHALLENGES</h3>
<p class="copy" style="left:101px;top:2512px;width:508px">Choosing the correct occupation plays an increasingly important role in our lives. Nowadays we consider an occupation as one of our fundamental rights. Yet, with the complexity of the modern technologies and job markets it is challenging to guarantee equal access to the market for everyone</p>
<a class="btn" style="left:103px;top:2685px;width:158px" href="#">Read More</a>
<div class="frame-back" style="left:662px;top:2400px;width:450px;height:405px;transform:rotate(6deg)"></div>
<div class="frame-img img-brain" style="left:674px;top:2402px;width:427px;height:393px" role="img" aria-label="Glowing digital brain above a circuit board"></div>

<div class="frame-back" style="left:84px;top:2890px;width:448px;height:405px;transform:rotate(-6deg)"></div>
<div class="frame-img img-circuit" style="left:99px;top:2896px;width:426px;height:395px" role="img" aria-label="Hand touching a circuit interface with a brain chip"></div>
<h3 class="block-title" style="left:591px;top:2945px;font-size:31px">HOW WE DO THIS</h3>
<p class="copy" style="left:593px;top:2994px;width:506px">We employ machine learning. Machines do not have personal preferences or biases. The impressive progress of natural language processing and deep neural networks power our algorithms to precisely recognize and extract the most important pieces of information. We use manually designed ontologies that set the frames of the analysis and guide the machine in this process.</p>
<a class="btn" style="left:593px;top:3192px;width:159px" href="#">Read More</a>

<div class="about-band"></div>
<h2 class="section-title" style="top:3487px">ABOUT US</h2>
<p class="about-copy" style="top:3556px">This application is a free social project powered by 3 enthusiast. We are experts in Natural Language Processing and Semantic Web with a record of 50+ scientific publications at top conferences and journals</p>
<p class="about-copy" style="top:3619px">We also have training and work experience in HR, and, most importantly passion for the job market.<br>We all have migrant backgrounds and we know how difficult and important it might be to find your place in any new professional environment. Therefore, we strive to provide better professional opportunities, equal access and fair treatment for everyone.</p>
<a class="btn" style="left:521px;top:3743px;width:158px" href="#">Read More</a>
<div class="team-photo ph-1" style="left:134px" role="img" aria-label="Portrait of team member one"></div>
<div class="team-photo ph-2" style="left:448px" role="img" aria-label="Portrait of team member two"></div>
<div class="team-photo ph-3" style="left:763px" role="img" aria-label="Portrait of team member three"></div>
<a class="btn" style="left:521px;top:4119px;width:158px" href="#">Donate</a>

<h2 class="section-title" style="top:4258px">INFORMATION SOURCES</h2>
<div class="source" style="left:382px;top:4398px"><i></i>Civic Data Office</div>
<div class="source" style="left:720px;top:4398px"><i></i>OPENFACTS</div>

<footer class="site-footer">
  <div class="f-head" style="left:99px">Contact Us</div>
  <div class="f-text" style="left:99px;top:98px">Lorem ipsum dolor sit amet,<br>consectetur adipiscing elit, sed do</div>
  <div class="f-text" style="left:99px;top:167px">hello@talentmap.example</div>
  <div class="f-text" style="left:99px;top:211px">+1 555 010 2040</div>

  <div class="f-head" style="left:408px">Email Us</div>
  <div class="f-text" style="left:408px;top:98px">Lorem ipsum dolor sit amet,<br>consectetur adipiscing elit, sed do</div>
  <div class="f-input"><span>Enter Your Email Address</span><svg width="14" height="14" viewBox="0 0 14 14"><path d="M1 7 13 1 10 13 7 8z" fill="var(--accent)"/></svg></div>

  <div class="f-head" style="left:803px">Links</div>
  <div class="f-text" style="left:803px;top:98px">Home<br>Early career<br>Skill trends<br>Skills</div>

  <div class="f-head" style="left:990px">Follow Us</div>
  <div class="f-text" style="left:990px;top:98px">Chirper<br>Worklink</div>

  <div class="copyright">Copyrights© Company Name. 2021 | Allrights Reserved.Terms, Privacy</div>
</footer>

</body>
</html>
```